Flyer für Therapie- und Gesundheitsdienstleister
Immer wieder gern. Kann ich nur weiterempfehlen!
Zielgruppe
Therapie- und Gesundheitsdienstleister im Bereich Physiotherapie, Podologie, Prävention und betriebliche Gesundheitsförderung. Für dieses Projekt möchten wir einen Flyer erstellen lassen für die Bewerbung der betrieblichen Gesundheitsförderungen in bzw. für Firmen
Aufgabenstellung
Klare Strukturen, nicht verspielt, DINA4 oder DINA5; leicht medizinischer Touch, evntuell Stockfotos integrieren, edel und hochwertiges Design

```html
<!DOCTYPE html>
<html lang="de">
<head>
<meta charset="utf-8">
<title>Betriebliche Gesundheitsförderung – Flyer</title>
<link href="https://fonts.googleapis.com/css2?family=Montserrat:wght@400;500;600;700&display=swap" rel="stylesheet">
<style>
  :root {
    --green: #3fa535;
    --orange: #ef7d00;
    --ink: #2f2f2f;
    --ink-soft: #3c3c3c;
    --footer: #58585a;
    --page-bg: #f1f2f3;
    --white: #ffffff;
  }
  * { margin: 0; padding: 0; box-sizing: border-box; }
  html, body { width: 1200px; height: 806px; overflow: hidden; background: var(--white); }
  body { position: relative; font-family: 'Montserrat', Arial, sans-serif; color: var(--ink); }

  .page {
    position: absolute; top: 39px; width: 513px; height: 725px; overflow: hidden;
    background: linear-gradient(180deg, #f7f7f8 0%, var(--page-bg) 55%, #e6e7e9 100%);
  }
  .page--front { left: 47px; }
  .page--back { left: 639px; }

  .footer-bar {
    position: absolute; left: 0; right: 0; bottom: 0; height: 25px;
    background: var(--footer); color: var(--white);
    font-size: 9.5px; font-weight: 600; text-align: center; line-height: 25px;
  }

  /* Front page */
  .hero-photo {
    position: absolute; left: 0; top: 0; width: 513px; height: 444px;
    background: linear-gradient(90deg, #f3f6f5 0%, #e9eeec 30%, #c9c3b9 52%, #5d554d 68%, #8c8479 80%, #d7dbdc 100%);
  }
  .hero-fade {
    position: absolute; left: 0; top: 0; width: 300px; height: 444px;
    background: linear-gradient(90deg, rgba(255,255,255,0.75) 0%, rgba(255,255,255,0.35) 70%, rgba(255,255,255,0) 100%);
  }
  .headline {
    position: absolute; left: 29px; top: 56px; white-space: nowrap;
    color: var(--green); font-size: 23px; font-weight: 700; line-height: 27px;
  }
  .intro {
    position: absolute; left: 29px; top: 123px; white-space: nowrap;
    font-size: 12px; line-height: 17.3px; color: var(--ink);
  }
  .intro b { font-weight: 700; }

  .benefit-box {
    position: absolute; left: 24px; top: 267px; width: 307px; height: 134px;
    background: rgba(255,255,255,0.88); border-radius: 8px;
    box-shadow: 0 2px 8px rgba(0,0,0,0.08);
    font-size: 10.2px; white-space: nowrap;
  }
  .benefit-box .lead { position: absolute; left: 16px; top: 10px; line-height: 14px; }
  .benefit {
    position: absolute; left: 47px; font-size: 9.8px; font-weight: 700; line-height: 14px; color: var(--ink-soft);
  }
  .benefit-num {
    position: absolute; left: 14px; width: 24px; height: 24px; border-radius: 50%;
    background: var(--orange); color: var(--white); font-weight: 700; font-size: 12px;
    text-align: center; line-height: 24px;
  }
  .benefit-box .closing { position: absolute; left: 16px; top: 94px; line-height: 14.6px; }

  .body-copy {
    position: absolute; left: 30px; top: 488px; white-space: nowrap;
    font-size: 10.9px; line-height: 14.6px;
  }
  .body-copy--strong { top: 603px; font-weight: 700; color: #1f1f1f; }

  /* Back page */
  .team-photo {
    position: absolute; left: 0; top: 0; width: 513px; height: 142px;
    background: linear-gradient(90deg, #e4e2df 0%, #d2cfcb 30%, #8c8a88 48%, #d88a6a 65%, #e9d9cf 80%, #efc9c2 100%);
  }
  .photo-curve { position: absolute; left: 0; top: 0; }
  .cta-badge {
    position: absolute; left: 89px; top: 58px; width: 100px; height: 100px; border-radius: 50%;
    background: var(--orange); color: var(--white);
    display: flex; align-items: center; justify-content: center; text-align: center;
    font-size: 9.6px; font-weight: 700; line-height: 13.5px; transform: rotate(-5deg);
    box-shadow: 0 2px 6px rgba(0,0,0,0.18);
  }
  .section-title {
    position: absolute; left: 28px; top: 180px; font-size: 18px; font-weight: 600; color: var(--ink-soft);
  }
  .pill {
    position: absolute; width: 215px; height: 21px; border-radius: 11px; background: var(--green);
    color: var(--white); font-size: 10.6px; font-weight: 600; line-height: 21px; padding-left: 11px;
  }
  .col-text { position: absolute; font-size: 8.6px; line-height: 12.9px; color: var(--ink-soft); white-space: nowrap; }
  .col-text ul { list-style: none; }
  .list li { position: relative; padding-left: 5px; margin-bottom: 2.4px; }
  .list li::before { content: "·"; position: absolute; left: 0; }

  .costs { position: absolute; left: 30px; top: 568px; font-size: 8.4px; line-height: 11.2px; white-space: nowrap; }
  .costs h3 { font-size: 10.8px; font-weight: 600; margin-bottom: 3px; }
  .costs p { margin-bottom: 3.5px; }

  .brand { position: absolute; left: 339px; top: 578px; display: flex; align-items: center; gap: 9px; }
  .brand-dot { width: 40px; height: 40px; border-radius: 50%; background: var(--green); }
  .brand-name { font-size: 16px; font-weight: 500; color: #555; line-height: 20px; }
  .contact { position: absolute; left: 342px; top: 637px; font-size: 8.6px; font-weight: 700; line-height: 10.5px; color: var(--ink-soft); white-space: nowrap; }
  .contact p + p { margin-top: 4px; }
</style>
</head>
<body>

<section class="page page--front">
  <div class="hero-photo" role="img" aria-label="Foto: lachende Kollegin mit Brille gibt einem Kollegen ein High Five im hellen Büro"></div>
  <div class="hero-fade"></div>

  <h1 class="headline">Betriebliche<br>Gesundheitsförderung</h1>
  <p class="intro">Die betriebliche Gesundheitsförderung<br>hat das Ziel die <b>Gesundheit der</b><br><b>Mitarbeiter</b> zu erhalten und zu fördern<br>sowie die <b>Leistungsfähigkeit und</b><br><b>Motivation</b> der Belegschaft<br>zu steigern.</p>

  <div class="benefit-box">
    <p class="lead">Immer mehr gewinnen jedoch folgende Punkte an</p>
    <span class="benefit-num" style="top:29px">1.</span>
    <p class="benefit" style="top:34px">Mitarbeiterbindung &amp;</p>
    <span class="benefit-num" style="top:63px">2.</span>
    <p class="benefit" style="top:59px">Arbeitgeber Attraktivität zu erhöhen,<br>um ein Vorteil am Bewerbermarkt zu erzielen.</p>
    <p class="closing">Auch da können wir Sie mit unserem Know-How und<br>abgerundeten Konzept unterstützen.</p>
  </div>

  <p class="body-copy">In regelmäßigen Abständen setzen wir uns mit Ihren Mitarbeitern<br>in Verbindung und erfragen den jeweiligen IST Stand und besprechen<br>gemeinsames Vorgehen, um gesundheitliche Problematiken im<br>Handlungsfeld Bewegung und Entspannung präventiv vorzubeugen.<br>Ihre Mitarbeiter werden dadurch in festen monatlichen Intervallen<br>sensibilisiert dass Sie sich um das Wohlbefinden Ihrer Mitarbeiter<br>kümmern und Sie auch darin investieren.</p>
  <p class="body-copy body-copy--strong">Sie als Arbeitgeber können nicht wissen und auch zeitlich nicht<br>gewährleisten welche individuellen gesundheitlichen Problematiken<br>Ihre Mitarbeiter haben. Deshalb bieten wir Ihnen eine individuelle Lösung<br>an Dienstleistung, welche den individuellen Bedarf Ihrer Mitarbeiter deckt.</p>

  <div class="footer-bar">www.bewegung-plus-halden.de</div>
</section>

<section class="page page--back">
  <div class="team-photo" role="img" aria-label="Foto: lächelnde Therapeutin mit roten Haaren und Brille im Trainingsraum mit Geräten"></div>
  <svg class="photo-curve" width="513" height="142" viewBox="0 0 513 142" aria-hidden="true">
    <path d="M0 0 C0 80 50 142 160 142 L0 142 Z" fill="#f7f7f8"/>
  </svg>
  <div class="cta-badge">Jetzt einen<br>persönlichen<br>Termin<br>vereinbaren!</div>

  <h2 class="section-title">Unsere Leistungen</h2>

  <div class="pill" style="left:18px; top:222px">Messung &amp; Analysen</div>
  <div class="col-text" style="left:29px; top:248px">
    <ul class="list">
      <li>Messung &amp; Analysen zur individuellen Stress- und<br>Resilienzdiagnostik um zielorientiert ein Streß-<br>managment in Ihrem Betrieb zu implementieren.</li>
      <li>Dokumentation von Körperdaten und Risikofaktoren<br>in einer Eingangskontrolle und einem ½ jährlichen<br>Wiederholung der Kontrolle.</li>
      <li>Wirbelsäulen- und Haltungsscreenings, Haltung,<br>Beweglichkeit und Haltungskomponenten werden<br>anschaulich dargestellt und bilden die Basis für<br>zielführende Visualisierung und fundierte<br>Übungsempfehlung.</li>
      <li>Analysen von Körperstabilität und Gleichgewicht;<br>Balance Check Plus ist ein erprobtes Analysetool<br>für das Thema Körperstabilität</li>
    </ul>
  </div>

  <div class="pill" style="left:18px; top:445px">Digitaler Gesundheitscoach</div>
  <div class="col-text" style="left:29px; top:471px">
    <ul class="list">
      <li>Workouts</li>
      <li>Live Online- Kurse</li>
      <li>Physio Übungen gezielt und individuell in der<br>Einzelberatung online und persönlich abgestimmt</li>
      <li>Online Präventionscoach</li>
    </ul>
  </div>

  <div class="pill" style="left:272px; top:222px">Bewegungsprogramme:</div>
  <div class="col-text" style="left:281px; top:248px">
    <p style="margin-bottom:2.4px">Präventionsprogramme nach §20 zertifiziert<br>von den Krankenkassen wie zum Beispiel:</p>
    <ul class="list">
      <li>Entspannungskurse Hatha Yoga</li>
      <li>Pilates</li>
      <li>Rückengymnastik</li>
      <li>Ganzkörper Training an Geräten</li>
      <li>Fit am Arbeitsplatz</li>
      <li>Online-Präventionskurs<br>(zeitlich und räumlich unabhängig)</li>
      <li>und einige mehr....</li>
    </ul>
  </div>

  <div class="pill" style="left:272px; top:405px">Mentale Gesundheit</div>
  <div class="col-text" style="left:283px; top:430px">
    <p style="margin-bottom:2.4px">Programme zur Achtsamkeit, Entspannung,<br>und Wahrnehmung. In Kleingruppen, Online<br>oder als Einzelleistung buchbar</p>
    <ul class="list"><li>Online Präventionscoach</li></ul>
  </div>

  <div class="pill" style="left:272px; top:495px">Gesundheitstage für Firmen</div>
  <div class="col-text" style="left:283px; top:521px">
    <p>Individuell auf Ihre Firma abgestimmt.</p>
  </div>

  <div class="costs">
    <h3>Informationen zu den Kosten</h3>
    <p>Bis zu 600 € können Sie, als Arbeitgeber steuerfrei bezuschussen.<br>Voraussetzung dafür ist, dass die fachlichen Anforderungen des<br>GKV- Spitzenverbandes erfüllt werden.</p>
    <p>Diese Leistungen können wir erfüllen und einige mehr on Top.<br>Lassen Sie sich persönlich und individuell beraten und nehmen<br>Sie persönlich oder via E-Mail Kontakt mit uns auf.</p>
    <p>Senden Sie uns eine E-Mail an info@bewegung-plus-halden.de und<br>wir melden uns umgehend für eine kostenlose Beratung.</p>
  </div>

  <div class="brand">
    <span class="brand-dot"></span>
    <span class="brand-name">Zentrum<br>Vitalwerk</span>
  </div>
  <div class="contact">
    <p>Lindenweg 14b<br>47110 Halden</p>
    <p>01234 - 56 78 90<br>info@bewegung-plus-halden.de</p>
  </div>

  <div class="footer-bar">www.bewegung-plus-halden.de</div>
</section>

</body>
</html>
```